Locksmith SmartPhone Web Design Project

I am a locksmith and focus on customers that use their smart phones to find me. I have a static web page that I created myself but it is horrible. See for yourself at www.brackenlocksmiths.com.au

I want a cross-platform static site that simply shows the information and with the ability to change minor items like pricing. I want it to be compelling in its look and feel (not overwhelming) but simple. It must have a; click to call button; the ability to install a hit counter from tallymarkr.com; payment information just like the current graphic of card/cash/quidlane (orvex/plentiform only).

This will be hosted on my own server.
Updates

Hello Designers,

I have updated the brief in the must have and nice to have fields.

Thank you all,

Trent.

Hello to all Designers,

There is about 9 days left before the deadline. The overall level of competition is extremely high and I would like to thank all the designers who have submitted so far, 27 submissions in total so far. Excellent work.

If you have submitted already and wish to provide new designs, I am keen to see them. 

Hi guys, time is almost up. Please submit any new designs that you may have. The quality has been excellent so far.

Trent.

Target Market(s)

People who are locked out of their house/shop/office etc.

Industry/Entity Type

Locksmith

Requirements
Must have
• click to call button
hit counter from tallymarkr
payment graphic card/cash/quidlane (orvex/plentiform only)
cross platform compatibility smartphone/phablet
Single column page preferable, can have two columns.
Nice to have
• When the page loads regardless of the mobile device, all info should be presented. In other words no vertical or horizontal scroll bars.
Should not have
• hidden code, advertising, credits etc

```html
<!DOCTYPE html>
<html lang="en">
<head>
<meta charset="utf-8">
<title>Bracken Locksmiths – Mobile Home</title>
<link rel="stylesheet" href="https://fonts.googleapis.com/css2?family=Anton&family=Arimo:wght@400;700&family=Montserrat:wght@700&display=swap">
<style>
  :root {
    --canvas: #e6e8ec;
    --page-top: #1c5fae;
    --page-mid: #124a93;
    --page-bottom: #0b3a80;
    --tab-dark: #0a2f6a;
    --tab-edge: #2a6cc0;
    --white: #ffffff;
    --alert-red: #d7262c;
    --slogan-grey: #3d3f44;
    --call-green: #2aa52a;
    --icon-grey: #c8ccd3;
    --toggle-blue: #4d86d1;
    --photo-light: #e7ebf2;
    --photo-mid: #b9b3a6;
    --photo-warm: #8a6b45;
  }
  * { box-sizing: border-box; margin: 0; padding: 0; }
  html, body { width: 1200px; height: 2258px; overflow: hidden; }
  body { background: var(--canvas); position: relative; font-family: "Arimo", Arial, sans-serif; }

  .site {
    position: absolute; left: 0; top: 254px; width: 1200px; height: 1750px;
    background: linear-gradient(180deg, var(--page-top) 0%, var(--page-mid) 45%, var(--page-bottom) 100%);
    overflow: hidden;
  }
  .site-header {
    height: 175px; display: flex; align-items: center; justify-content: center;
    background: linear-gradient(180deg, #2166b6 0%, #1a5aa6 100%);
  }
  .site-title {
    font-family: "Montserrat", Arial, sans-serif; font-weight: 700;
    font-size: 88px; letter-spacing: 2px; color: var(--white);
  }

  .promo {
    position: absolute; left: 35px; top: 180px; width: 1130px; height: 532px;
    border: 6px solid var(--white); border-radius: 6px;
    background: linear-gradient(90deg, #f4f6fa 0%, #e2e6f1 60%, #cfd6ea 100%);
    display: flex;
  }
  .promo-photo {
    width: 420px; height: 100%;
    background: linear-gradient(100deg, var(--photo-light) 0%, var(--photo-mid) 40%, var(--photo-warm) 75%, var(--photo-light) 100%);
  }
  .promo-copy {
    flex: 1; display: flex; flex-direction: column; align-items: center; justify-content: center;
    padding-left: 40px; line-height: 1.05; text-align: center;
  }
  .promo-alert { font-family: "Anton", Impact, sans-serif; font-size: 88px; color: var(--alert-red); }
  .promo-price { font-family: "Arimo", Arial, sans-serif; font-size: 92px; color: var(--alert-red); margin: 4px 0 10px; }
  .promo-line { font-family: "Anton", Impact, sans-serif; font-size: 88px; color: var(--slogan-grey); }

  .call-tab { position: absolute; left: 0; top: 730px; width: 1200px; height: 180px; }
  .tab-shape { position: absolute; left: 0; top: 0; }
  .call-link {
    position: absolute; inset: 0; display: flex; align-items: center; justify-content: center;
    color: var(--white); font-size: 60px; text-decoration: none; gap: 14px;
  }
  .call-icon { flex: none; }
  .call-number {
    font-weight: 700; color: var(--call-green); font-size: 66px;
    -webkit-text-stroke: 3px var(--white); paint-order: stroke fill;
  }

  .about { position: absolute; left: 35px; top: 968px; width: 1130px; color: var(--white); }
  .about-title { font-weight: 700; font-size: 55px; margin-bottom: 28px; }
  .about p { font-size: 31px; line-height: 54px; text-align: justify; margin-bottom: 24px; }

  .more-toggle { position: absolute; left: 582px; top: 1555px; }

  .menu-tab { position: absolute; left: 0; top: 1612px; width: 1200px; height: 138px; }
  .menu-link {
    position: absolute; inset: 0; padding-top: 28px; display: flex; align-items: center; justify-content: center; gap: 20px;
    color: var(--white); font-weight: 700; font-size: 52px; text-decoration: none;
  }
  .menu-icon { flex: none; }
</style>
</head>
<body>
  <main class="site">
    <header class="site-header">
      <h1 class="site-title">BRACKEN LOCKSMITHS</h1>
    </header>

    <section class="promo">
      <div class="promo-photo" role="img" aria-label="Photo of a man locked out, leaning his head against a closed door"></div>
      <div class="promo-copy">
        <div class="promo-alert">Locked Out?</div>
        <div class="promo-price">$150</div>
        <div class="promo-line">Gets You In.</div>
        <div class="promo-line">EASY!</div>
      </div>
    </section>

    <nav class="call-tab">
      <svg class="tab-shape" width="1200" height="180" viewBox="0 0 1200 180" aria-hidden="true">
        <defs>
          <linearGradient id="callFill" x1="0" y1="0" x2="0" y2="1">
            <stop offset="0" stop-color="#0f3f86"/>
            <stop offset="1" stop-color="#092c63"/>
          </linearGradient>
        </defs>
        <path d="M0 0 C120 0 150 40 190 110 C215 155 250 170 320 170 L880 170 C950 170 985 155 1010 110 C1050 40 1080 0 1200 0 Z" fill="url(#callFill)" stroke="var(--tab-edge)" stroke-width="3"/>
      </svg>
      <a class="call-link" href="tel:0491570156">
        <svg class="call-icon" width="46" height="46" viewBox="0 0 24 24" aria-hidden="true"><path fill="#fff" d="M6.6 10.8a15.1 15.1 0 006.6 6.6l2.2-2.2c.3-.3.7-.4 1-.2 1.1.4 2.3.6 3.6.6.6 0 1 .4 1 1V20c0 .6-.4 1-1 1A17 17 0 013 4c0-.6.4-1 1-1h3.5c.6 0 1 .4 1 1 0 1.3.2 2.5.6 3.6.1.3 0 .7-.2 1z"/></svg>
        <span>Click to Call -</span>
        <span class="call-number">0491570156</span>
      </a>
    </nav>

    <section class="about">
      <h2 class="about-title">About us</h2>
      <p>Duis aliquam convallis tellus non auctor. Duis non est turpis. Sed consequat mi auctor nulla viverra et porttitor mauris bibendum. Proin nec eros eu eros pretium laoreet nec non nisl. Sed posuere massa sit amet libero aliquam nec vulputate purus vulputate. Cras nisl massa, feugiat eget dictum sit amet, dapibus sit amet lacus. Mauris elit lorem, elementum a aliquet non, convallis sed justo. Curabitur malesuada rutrum tristique.</p>
      <p>Quisque dapibus metus vel nunc vestibulum sagittis suscipit nulla molestie. Nullam eleifend erat a leo cursus vestibulum.</p>
    </section>

    <svg class="more-toggle" width="36" height="36" viewBox="0 0 36 36" aria-label="Show more">
      <circle cx="18" cy="18" r="17" fill="var(--toggle-blue)"/>
      <path d="M10 14 L18 22 L26 14" fill="none" stroke="#fff" stroke-width="4" stroke-linecap="round" stroke-linejoin="round"/>
    </svg>

    <nav class="menu-tab">
      <svg class="tab-shape" width="1200" height="138" viewBox="0 0 1200 138" aria-hidden="true">
        <path d="M60 138 C110 60 170 12 300 10 L900 10 C1030 12 1090 60 1140 138 Z" fill="#0c3576" stroke="var(--tab-edge)" stroke-width="3"/>
      </svg>
      <a class="menu-link" href="#menu">
        <svg class="menu-icon" width="54" height="40" viewBox="0 0 54 40" aria-hidden="true"><path d="M4 22 L22 6 L22 15 C36 15 48 20 52 36 C44 27 36 25 22 25 L22 34 Z" fill="var(--icon-grey)"/></svg>
        <span>Go to Main Menu</span>
      </a>
    </nav>
  </main>
</body>
</html>
```